Help our Sugar Loom find our winning design! We're looking for a business card....

We’re a Sugar Loom in NY specializing in custom-made cakes and unique desserts.
Our cakes combine flavor and art, each designed to match customer’s special event and theme.
We’d like a unique business card with a clean design that will combine French chic and artistic look & feel.
We’d like to differentiate ourselves from standard bakeries, please don’t offer cupcake images :-)
Our logo is peach-pink and brown and we’d love to use these colors ( . Another color that can be added is gold - or feel free to suggest!

Target Market(s)

Women, ages 25-55

Industry/Entity Type

Boutique

Contact Information for Business Card

Text on card:
Logo
Sugar Loom by Dana Welch

www.sugarloomsweets.com
hello@sugarloom.com
(516) 555-0147
F – sugarloomnyc
IG - sugarloom_ny

Font styles to use
Sans Serif
Script

Requirements
Must have
• Logo
• Clean look
• French chic and artistic look & feel.
Nice to have
• Damask pattern
Should not have
• Cupcake images

```html
<!DOCTYPE html>
<html lang="en">
<head>
<meta charset="utf-8">
<title>Sugar Loom — Business Card</title>
<link rel="stylesheet" href="https://fonts.googleapis.com/css2?family=Lora:wght@400;500&family=Montserrat:wght@600&display=swap">
<style>
  :root {
    --backdrop: #c9c9c9;
    --card-white: #ffffff;
    --blush: #dfaca4;
    --blush-deep: #d49a91;
    --cocoa: #3b2926;
    --cocoa-soft: #4a3632;
    --rule: #2b1f1d;
  }
  * { box-sizing: border-box; margin: 0; padding: 0; }
  html, body {
    width: 1200px; height: 852px; overflow: hidden;
    background: var(--backdrop);
  }
  .stage {
    position: relative; width: 1200px; height: 852px;
    display: flex; align-items: center; justify-content: center; gap: 60px;
  }
  .card {
    position: relative; width: 520px; height: 300px;
    background: var(--card-white);
    border-radius: 22px; overflow: hidden;
    box-shadow: 0 6px 18px rgba(0,0,0,0.18);
  }
  .brand {
    position: absolute; left: 0; right: 0;
    display: flex; flex-direction: column; align-items: center;
  }
  .card--front .brand { top: 112px; }
  .card--back .brand { top: 38px; }
  .brand__name {
    display: flex; align-items: center; gap: 12px;
    font-family: "Lora", serif; font-weight: 400;
    font-size: 42px; color: var(--cocoa); letter-spacing: 0.5px;
  }
  .brand__dot {
    width: 12px; height: 12px; border-radius: 50%;
    background: var(--blush-deep);
  }
  .brand__tagline {
    margin-top: 8px;
    font-family: "Montserrat", sans-serif; font-weight: 600;
    font-size: 10px; letter-spacing: 3px; color: var(--cocoa);
  }
  .contact-band {
    position: absolute; left: 0; right: 0; bottom: 0; height: 142px;
    background: var(--blush);
    border-top: 2px solid var(--rule);
    padding: 30px 30px 0 30px;
    display: flex; justify-content: space-between;
    font-family: "Lora", serif; font-size: 15px; color: var(--cocoa-soft);
  }
  .contact-list, .social-list { list-style: none; }
  .contact-list { align-self: flex-end; padding-bottom: 24px; }
  .contact-list li, .social-list li {
    display: flex; align-items: center; gap: 10px; line-height: 22px;
  }
  .contact-icon { width: 14px; height: 14px; flex: none; }
  .social-mark {
    width: 11px; height: 11px; border-radius: 2px;
    background: var(--cocoa); flex: none;
  }
</style>
</head>
<body>
<main class="stage">

  <section class="card card--front" aria-label="Card front">
    <div class="brand">
      <div class="brand__name"><span>Sugar Loom</span><span class="brand__dot"></span></div>
      <div class="brand__tagline">HANDCRAFTED WITH LOVE</div>
    </div>
  </section>

  <section class="card card--back" aria-label="Card back">
    <div class="brand">
      <div class="brand__name"><span>Sugar Loom</span><span class="brand__dot"></span></div>
      <div class="brand__tagline">HANDCRAFTED WITH LOVE</div>
    </div>

    <div class="contact-band">
      <ul class="contact-list">
        <li>
          <svg class="contact-icon" viewBox="0 0 16 16" aria-hidden="true">
            <path fill="#3b2926" d="M3 1.5h3l1.2 3.2-1.8 1.2a9 9 0 0 0 4.7 4.7l1.2-1.8 3.2 1.2v3a1.5 1.5 0 0 1-1.5 1.5A13 13 0 0 1 1.5 3 1.5 1.5 0 0 1 3 1.5z"/>
          </svg>
          <span>(516) 555-0147</span>
        </li>
        <li>
          <svg class="contact-icon" viewBox="0 0 16 16" aria-hidden="true">
            <circle cx="8" cy="8" r="6.5" fill="none" stroke="#3b2926" stroke-width="1.4"/>
            <path d="M1.5 8h13M8 1.5c-3 3.5-3 9.5 0 13M8 1.5c3 3.5 3 9.5 0 13" fill="none" stroke="#3b2926" stroke-width="1.2"/>
          </svg>
          <span>www.sugarloomsweets.com</span>
        </li>
        <li>
          <svg class="contact-icon" viewBox="0 0 16 16" aria-hidden="true">
            <rect x="1.5" y="3.5" width="13" height="9" rx="1" fill="#3b2926"/>
            <path d="M2 4.5l6 4.5 6-4.5" fill="none" stroke="#dfaca4" stroke-width="1.2"/>
          </svg>
          <span>hello@sugarloom.com</span>
        </li>
      </ul>

      <ul class="social-list">
        <li><span class="social-mark"></span><span>sugarloomnyc</span></li>
        <li><span class="social-mark"></span><span>sugarloom_ny</span></li>
      </ul>
    </div>
  </section>

</main>
</body>
</html>
```